VENTURE CAPITAL GROUP BUSINESS CARD DESIGN

Venture Capital Group based in SF looking for a bold business card design. No trendy colour explosion, 3D effects etc. Just "simple" optical effects. Works on your brain, keeps your eye focused and sticks to your mind.
Target Market(s)
Technology startups
Industry/Entity Type
Venture Capital
Contact Information for Business Card
DESMOND WHITLAKE
MANAGING PARTNER
187 FENWORTH ST SAN FRANCISCO, CA 94187
415.555.0142 O
415.555.0147 F
415.555.0193 C
desmond@veldtmoorcapital.ventures

```html
<!DOCTYPE html>
<html lang="en">
<head>
<meta charset="utf-8">
<title>Veldtmoor Capital Group – Business Card</title>
<link rel="stylesheet" href="https://fonts.googleapis.com/css2?family=Cinzel:wght@400&family=Open+Sans:wght@400;600&display=swap">
<style>
  :root {
    --backdrop: #141414;
    --green-light: #58b953;
    --green-mid: #2f8a34;
    --green-dark: #0a4613;
    --brand-green: #1b7a2b;
    --subtitle-grey: #9a9a9a;
    --white: #ffffff;
    --soft-white: #eef1ee;
    --mark-grey: #e6e6e6;
    --divider: rgba(255,255,255,0.22);
  }
  * { margin: 0; padding: 0; box-sizing: border-box; }
  html, body {
    width: 1200px; height: 900px; overflow: hidden;
    background: var(--backdrop);
    font-family: "Open Sans", Arial, sans-serif;
  }
  .stage { position: relative; width: 1200px; height: 900px; }
  .card {
    position: absolute; top: 306px; height: 270px;
    border-radius: 10px; overflow: hidden;
  }
  .card-front {
    left: 149px; width: 438px;
    background: linear-gradient(180deg, var(--green-light) 0%, var(--green-mid) 45%, var(--green-dark) 100%);
    color: var(--white);
  }
  .card-back { left: 608px; width: 440px; background: var(--white); }

  .front-dot {
    position: absolute; left: 27px; top: 77px;
    width: 120px; height: 120px; border-radius: 50%;
    background: var(--soft-white);
  }
  .divider {
    position: absolute; left: 178px; top: 66px; width: 1px; height: 150px;
    background: var(--divider);
  }
  .contact { position: absolute; left: 202px; top: 57px; }
  .contact .name { font-size: 15.5px; font-weight: 600; line-height: 20px; }
  .contact .role { font-size: 11.5px; line-height: 16px; }
  .contact .address { margin-top: 13px; font-size: 12px; line-height: 15.5px; }
  .contact .lines { margin-top: 10px; list-style: none; font-size: 12px; line-height: 18px; }
  .contact .lines li { display: flex; align-items: center; gap: 4px; }
  .contact .lines svg { width: 9px; height: 9px; fill: var(--white); flex: none; }

  .back-dot {
    position: absolute; left: 160px; top: 46px;
    width: 116px; height: 116px; border-radius: 50%;
    background: var(--mark-grey);
  }
  .back-name {
    position: absolute; left: 0; right: 0; top: 172px;
    text-align: center;
    font-family: "Cinzel", Georgia, serif;
    font-weight: 400; font-size: 36px; line-height: 40px;
    letter-spacing: 0.5px;
    color: var(--brand-green);
  }
  .back-subtitle {
    position: absolute; left: 0; right: 0; top: 213px;
    text-align: center;
    font-family: "Cinzel", Georgia, serif;
    font-size: 8.5px; line-height: 10px;
    letter-spacing: 4.5px;
    text-transform: uppercase;
    color: var(--subtitle-grey);
  }
</style>
</head>
<body>
<main class="stage">
  <section class="card card-front" aria-label="Card front">
    <span class="front-dot"></span>
    <span class="divider"></span>
    <div class="contact">
      <p class="name">Desmond Whitlake</p>
      <p class="role">Managing Partner</p>
      <p class="address">187 Fenworth St San<br>Francisco, CA 94187</p>
      <ul class="lines">
        <li><svg viewBox="0 0 10 10" aria-hidden="true"><path d="M2 0.5 L3.6 0.5 L4.3 2.8 L3.2 3.8 Q4.2 5.8 6.2 6.8 L7.2 5.7 L9.5 6.4 L9.5 8 Q9.5 9.5 8 9.5 Q0.5 9 0.5 2 Q0.5 0.5 2 0.5Z"/></svg>415.555.0142</li>
        <li><svg viewBox="0 0 10 10" aria-hidden="true"><path d="M2.5 0.5 H7 V3 H9.5 V9.5 H0.5 V3 H2.5Z M3.5 1.5 V3 H6 V1.5Z M2 5 V6 H8 V5Z M2 7 V8 H8 V7Z" fill-rule="evenodd"/></svg>415.555.0147</li>
        <li><svg viewBox="0 0 10 10" aria-hidden="true"><path d="M2.5 0 H7.5 V10 H2.5Z M3.3 1 V8 H6.7 V1Z" fill-rule="evenodd"/></svg>415.555.0193</li>
        <li><svg viewBox="0 0 10 10" aria-hidden="true"><path d="M0 2 H10 V8.5 H0Z M0.8 2.6 L5 5.6 L9.2 2.6" fill-rule="evenodd"/></svg>desmond@veldtmoorcapital.ventures</li>
      </ul>
    </div>
  </section>

  <section class="card card-back" aria-label="Card back">
    <span class="back-dot"></span>
    <p class="back-name">Veldtmoor</p>
    <p class="back-subtitle">Capital Group</p>
  </section>
</main>
</body>
</html>
```